Harbor Crestline (Business Card Design)

Need business cards designed. Something modern, chic, and sleek. Mabye the back of the card should be the navy blue that is in the logo and then just the logo on the back.

Target Market(s)

Those in the hotel, office, and renovation industry

Contact Information for Business Card

1. Logo 2. Dorian Fenwick 3. CEO/Founder 4. Phone: (833) HarbCre / (833) 427-2731 5. Email: dorian@theharborcrestline.com 6. Website: www.theharborcrestline.com

Font styles to use
Other font styles liked:
• Look at the logo font and base the font for everything else off of that.

Colors
0054AA
0677BA
7BADD7
CADEEF
E8F1F8

Requirements
Must have
• Colors that are associated in the logo
Nice to have
• Sleek modern clean and chic design.

```html
<!DOCTYPE html>
<html lang="en">
<head>
<meta charset="utf-8">
<title>Harbor Crestline – Business Card</title>
<link rel="stylesheet" href="https://fonts.googleapis.com/css2?family=Poppins:wght@400;500;600&display=swap">
<style>
  :root {
    --navy: #101a3d;
    --navy-ink: #121b44;
    --gold: #c9a03f;
    --grey-text: #555a60;
    --steel: #5f87ad;
    --paper: #ffffff;
    --backdrop: #d7d8da;
  }
  * { margin: 0; padding: 0; box-sizing: border-box; }
  html, body { width: 1200px; height: 959px; overflow: hidden; }
  body {
    background: var(--backdrop);
    font-family: "Poppins", sans-serif;
    position: relative;
  }
  .card {
    position: absolute;
    left: 295px;
    width: 612px;
    height: 352px;
    overflow: hidden;
  }
  .card--front { top: 103px; background: var(--paper); }
  .card--back { top: 499px; background: var(--navy); }

  .brand {
    position: absolute;
    display: flex;
    align-items: center;
    gap: 10px;
    font-weight: 600;
    letter-spacing: 0.06em;
    text-transform: uppercase;
    white-space: nowrap;
  }
  .brand__mark { width: 12px; height: 12px; flex: none; }
  .card--front .brand {
    left: 40px; top: 159px;
    font-size: 20px; color: var(--navy-ink);
  }
  .card--front .brand__mark { background: var(--gold); }

  .divider {
    position: absolute;
    left: 306px; top: 117px;
    width: 1.5px; height: 118px;
    background: var(--gold);
  }
  .contact { position: absolute; left: 319px; top: 108px; }
  .contact__name {
    font-size: 25px; font-weight: 600; line-height: 1.2;
    color: var(--navy-ink);
  }
  .contact__role {
    font-size: 15px; color: var(--gold); line-height: 1.2; margin-bottom: 14px;
  }
  .contact__list { list-style: none; }
  .contact__item {
    display: flex; align-items: center; gap: 5px;
    font-size: 14.6px; color: var(--grey-text); line-height: 22px;
    white-space: nowrap;
  }
  .contact__icon { width: 13px; height: 13px; flex: none; fill: var(--navy-ink); }

  .back-art {
    position: absolute; left: 0; top: 20px; width: 400px; height: 332px;
    background: linear-gradient(150deg, rgba(95,135,173,0.75) 0%, rgba(95,135,173,0.25) 60%, rgba(95,135,173,0) 100%);
  }
  .card--back .brand {
    left: 490px; top: 230px; transform: translateX(-50%);
    flex-direction: column; gap: 14px;
    font-size: 20px; color: var(--paper);
  }
  .card--back .brand__mark { background: var(--paper); }
</style>
</head>
<body>
  <section class="card card--front" aria-label="Business card front">
    <div class="brand"><span class="brand__mark"></span>Harbor Crestline</div>
    <div class="divider"></div>
    <div class="contact">
      <h1 class="contact__name">Dorian Fenwick</h1>
      <p class="contact__role">CEO/Founder</p>
      <ul class="contact__list">
        <li class="contact__item">
          <svg class="contact__icon" viewBox="0 0 24 24"><path d="M6.6 10.8c1.4 2.8 3.8 5.1 6.6 6.6l2.2-2.2c.3-.3.7-.4 1-.2 1.1.4 2.3.6 3.6.6.6 0 1 .4 1 1V20c0 .6-.4 1-1 1C10.6 21 3 13.4 3 4c0-.6.4-1 1-1h3.5c.6 0 1 .4 1 1 0 1.3.2 2.5.6 3.6.1.3 0 .7-.2 1z"/></svg>
          (833) HarbCre / (833) 427-2731 5
        </li>
        <li class="contact__item">
          <svg class="contact__icon" viewBox="0 0 24 24"><path d="M2 5h20v14H2z M2 5l10 8 10-8" fill="none" stroke="#121b44" stroke-width="0"/><path d="M2 5h20v2l-10 7L2 7z M2 9l6 4.5L2 18z M22 9v9l-6-4.5z M9.5 14.6L12 16.4l2.5-1.8L21.5 19h-19z"/></svg>
          dorian@theharborcrestline.com
        </li>
        <li class="contact__item">
          <svg class="contact__icon" viewBox="0 0 24 24" fill="none" stroke="#121b44" stroke-width="2"><circle cx="12" cy="12" r="9.5"/><ellipse cx="12" cy="12" rx="4" ry="9.5"/><path d="M2.5 12h19M4 7h16M4 17h16"/></svg>
          www.theharborcrestline.com
        </li>
      </ul>
    </div>
  </section>

  <section class="card card--back" aria-label="Business card back">
    <div class="back-art" role="img" aria-label="Large faded steel-blue brand decoration"></div>
    <div class="brand"><span class="brand__mark"></span>Harbor Crestline</div>
  </section>
</body>
</html>
```